Executive Business Card for Healthcare Company [Need Today]

I need a business card design for a healthcare company. The only branding the company has thus far is a logo. The cards will be utilized by company executives. The design I envision will be vibrant and appealing but with a corporate feel. They shouldn't be too casual or playful. I would like to complete this project TODAY if possible.

Target Market(s)

Healthcare vendors, other executives in healthcare and pharmaceuticals

Industry/Entity Type

Pharmaceutical

Contact Information for Business Card

See attachment

Font styles to use
Serif
Sans Serif

Colors

Designer to choose colors to be used in the design.

```html
<!DOCTYPE html>
<html lang="en">
<head>
<meta charset="utf-8">
<title>Corvane Therapeutics — Executive Business Card</title>
<link rel="stylesheet" href="https://fonts.googleapis.com/css2?family=Open+Sans:wght@400;500&family=Rubik:wght@400;500&display=swap">
<style>
  :root {
    --backdrop: #e4e4e2;
    --teal: #35bfc6;
    --teal-dark: #2fb3bb;
    --card-white: #ffffff;
    --ink: #4a4a4a;
    --ink-soft: #5a5a5a;
    --rule: #9a9a9a;
    --icon: #555555;
  }
  html, body {
    margin: 0;
    padding: 0;
    width: 1200px;
    height: 1000px;
    overflow: hidden;
    background: var(--backdrop);
  }
  .canvas {
    position: relative;
    width: 1200px;
    height: 1000px;
    font-family: "Open Sans", Arial, sans-serif;
  }
  .card {
    position: absolute;
    border-radius: 38px;
    box-shadow: 0 14px 24px rgba(0, 0, 0, 0.28);
    overflow: hidden;
  }
  .card-front {
    left: 150px;
    top: 102px;
    width: 628px;
    height: 356px;
    background: var(--teal);
  }
  .card-back {
    left: 372px;
    top: 546px;
    width: 636px;
    height: 362px;
    background: var(--card-white);
  }
  .wordmark {
    position: absolute;
    display: flex;
    align-items: center;
    gap: 12px;
  }
  .wordmark-circle {
    border-radius: 50%;
    flex: none;
  }
  .wordmark-name {
    display: flex;
    flex-direction: column;
    font-family: "Open Sans", Arial, sans-serif;
    font-weight: 400;
    font-size: 20px;
    line-height: 1.15;
    white-space: nowrap;
  }
  .card-front .wordmark {
    left: 354px;
    top: 140px;
  }
  .card-front .wordmark-circle {
    width: 74px;
    height: 74px;
    border: 2px solid var(--card-white);
  }
  .card-front .wordmark-name {
    color: var(--card-white);
  }
  .card-back .wordmark {
    left: 366px;
    top: 62px;
  }
  .card-back .wordmark-circle {
    width: 70px;
    height: 70px;
    border: 3px solid var(--teal);
  }
  .card-back .wordmark-name {
    color: var(--teal-dark);
  }
  .person-name {
    position: absolute;
    left: 42px;
    top: 70px;
    margin: 0;
    font-family: "Rubik", Arial, sans-serif;
    font-weight: 400;
    font-size: 32px;
    letter-spacing: 2px;
    color: var(--teal);
  }
  .person-title {
    position: absolute;
    left: 42px;
    top: 114px;
    margin: 0;
    font-family: "Rubik", Arial, sans-serif;
    font-size: 18px;
    color: var(--ink);
  }
  .divider {
    position: absolute;
    left: 40px;
    top: 177px;
    width: 557px;
    height: 0;
    border-top: 1.5px solid var(--rule);
  }
  .contact-list {
    position: absolute;
    left: 40px;
    top: 196px;
    margin: 0;
    padding: 0;
    list-style: none;
  }
  .contact-item {
    display: flex;
    align-items: center;
    height: 29px;
    font-size: 21px;
    letter-spacing: 0.6px;
    color: var(--ink-soft);
  }
  .contact-icon {
    width: 20px;
    height: 18px;
    margin-right: 18px;
    fill: var(--icon);
  }
  .company-block {
    position: absolute;
    left: 0;
    top: 303px;
    width: 636px;
    text-align: center;
    font-size: 16px;
    line-height: 20px;
    color: var(--teal);
  }
  .company-block p { margin: 0; }
</style>
</head>
<body>
<main class="canvas">

  <section class="card card-front" aria-label="Card front">
    <div class="wordmark">
      <span class="wordmark-circle"></span>
      <span class="wordmark-name"><span>Corvane</span><span>Therapeutics</span></span>
    </div>
  </section>

  <section class="card card-back" aria-label="Card back">
    <h1 class="person-name">Daniel Mercer</h1>
    <p class="person-title">Senior Director of Marketing</p>

    <div class="wordmark">
      <span class="wordmark-circle"></span>
      <span class="wordmark-name"><span>Corvane</span><span>Therapeutics</span></span>
    </div>

    <div class="divider"></div>

    <ul class="contact-list">
      <li class="contact-item">
        <svg class="contact-icon" viewBox="0 0 20 18" aria-hidden="true">
          <path d="M1 6c0-3 4-4 9-4s9 1 9 4v1h-5V5H6v2H1z"/>
          <path d="M5 8h10l3 9H2z"/>
          <circle cx="10" cy="12.5" r="2.4" fill="#fff"/>
        </svg>
        555-214-7730
      </li>
      <li class="contact-item">
        <svg class="contact-icon" viewBox="0 0 20 18" aria-hidden="true">
          <path d="M4 1l3 4-2 2c1 2 3 4 5 5l2-2 4 3-2 3C8 16 2 10 1 4z"/>
        </svg>
        555-382-1046
      </li>
      <li class="contact-item">
        <svg class="contact-icon" viewBox="0 0 20 18" aria-hidden="true">
          <path d="M1 4h18v1l-9 6-9-6z"/>
          <path d="M1 7l9 6 9-6v8H1z"/>
        </svg>
        dmercer@corvanerx.com
      </li>
    </ul>

    <div class="company-block">
      <p>CORVANE THERAPEUTICS, LLC</p>
      <p>118 N Lumpkin Avenue, Millbrook, GA 30412</p>
    </div>
  </section>

</main>
</body>
</html>
```